verdant terraces simple classy business card design

my name is colin barrow and I run a gardening business aimed at high class verdant terraces. the business name is verdant terraces and our logo was designed on pixel harbour .My clientel are anything from residential homes to businesses. I take pride in my work and know that I offer a service like no other in my area.
The business card will be used to represent my business and I want it to be not only rememberable, but simplistic and modern. Eye catching too. Of course I would like it relatable to gardening and appealing to the correct clientel - those being garden enthusiasts, prestigious homes and businesses that are after top of the line gardening services like no other on the market.
I am not a typical lawn mowing business so I don't want a typical card design that represents that. The gardens I work with are generally million dollar properties with owners who are very garden proud looking for upkeep and guidance from me along with sometimes whole new garden designs. I want the business cards to show to my clients that I take pride, as they do, in their garden. And I want them to know from my card that I am a professional, qualified horticulturist offering them a top of the line service for life. I want them to refer my business on. I want them to look at my business card and see class and professionalism in a modern unique bold way.
The card should be simple with the possibility of the logo on the front being embossed/debossed and my details on the back the card should have a organic garden feel it's very important to me that it is absolutely perfect
I am also very open to ideas and suggestions so look forward to seeing the designs. the business logo has been supplied with this project and I want the card to be double sided

Contact info is
Colin Barrow - Managing Director / Horticulturist
Phone : 0481 526 704
Email: colinbarrow@verdantterraces.example.au

Target Market(s)

high class gardens residential and commercial

Industry/Entity Type

Gardener

Contact Information for Business Card

Contact info is
Phone : 0481 526 704

PLEASE MAKE CARD DOUBLE SIDED

Requirements
Must have
• organic simple classy modern feel
• must flow with the current logo that has been supplied with this project
• Double sided
• Must explain in a simple way that I deal with high end gardens and I'm a qualified horticulturist
Nice to have
• embossed debossed logo
Should not have
• shouldn't be to busy or cheap looking

```html
<!DOCTYPE html>
<html lang="en">
<head>
<meta charset="utf-8">
<title>Verdant Terraces — Business Card</title>
<link href="https://fonts.googleapis.com/css2?family=Montserrat:wght@400;500&display=swap" rel="stylesheet">
<style>
  :root {
    --backdrop: #e7e8e9;
    --card-stock: #e2e3e5;
    --deboss: #d2d3d5;
    --leaf-green: #5f9e5c;
    --white: #ffffff;
  }
  * { box-sizing: border-box; margin: 0; padding: 0; }
  html, body {
    width: 1200px; height: 922px; overflow: hidden;
    background: var(--backdrop);
    font-family: "Montserrat", sans-serif;
  }
  .canvas { position: relative; width: 1200px; height: 922px; }

  .card { position: absolute; top: 86px; overflow: hidden; }

  .card-front {
    left: 154px; width: 432px; height: 756px;
    background: var(--card-stock);
    color: var(--leaf-green);
    text-align: center;
  }
  .wordmark {
    position: absolute; top: 150px; left: 0; width: 100%;
    display: flex; align-items: center; justify-content: center; gap: 14px;
    color: var(--deboss);
    font-weight: 400; font-size: 30px; letter-spacing: 0.14em;
    text-transform: uppercase; line-height: 38px;
  }
  .wordmark-dot {
    width: 18px; height: 18px; border-radius: 50%;
    background: var(--deboss); flex: none;
  }

  .contact { position: absolute; left: 0; width: 100%; white-space: nowrap; }
  .contact-name { top: 562px; height: 36px; line-height: 36px; font-weight: 500; font-size: 31px; }
  .contact-role { top: 600px; height: 24px; line-height: 24px; font-weight: 400; font-size: 19px; letter-spacing: 0.02em; }
  .contact-icons { top: 634px; height: 14px; display: flex; justify-content: center; gap: 6px; }
  .contact-phone, .contact-email { height: 24px; line-height: 24px; font-weight: 400; letter-spacing: 0.02em; }
  .contact-phone { top: 658px; font-size: 18px; }
  .contact-email { top: 682px; font-size: 17px; }

  .front-band {
    position: absolute; left: 0; bottom: 0; width: 100%; height: 26px;
    background: var(--leaf-green);
  }

  .card-back {
    left: 621px; width: 428px; height: 748px;
    background: var(--leaf-green);
    display: flex; align-items: center; justify-content: center; gap: 14px;
    color: var(--white);
  }
  .back-wordmark {
    font-weight: 400; font-size: 28px; letter-spacing: 0.14em;
    text-transform: uppercase; line-height: 36px; text-align: center;
  }
  .back-dot { width: 18px; height: 18px; border-radius: 50%; background: var(--white); flex: none; }
</style>
</head>
<body>
<main class="canvas">
  <section class="card card-front" aria-label="Card front">
    <div class="wordmark">
      <span class="wordmark-dot"></span>
      <span>Verdant<br>Terraces</span>
    </div>
    <p class="contact contact-name">Colin Barrow</p>
    <p class="contact contact-role">Managing Director / Horticulturist</p>
    <div class="contact contact-icons" aria-hidden="true">
      <svg width="12" height="14" viewBox="0 0 12 14" fill="none" stroke="currentColor" stroke-width="1.4" stroke-linecap="round" stroke-linejoin="round">
        <path d="M3 1.5 L5 4 L3.8 5.6 C4.5 7.6 5.8 9.2 7.6 10.3 L9 9 L11 11 L9.6 12.6 C5.4 11.8 2 7.6 1.6 3 Z"/>
      </svg>
      <svg width="14" height="14" viewBox="0 0 14 14" fill="none" stroke="currentColor" stroke-width="1.3" stroke-linejoin="round">
        <rect x="1.5" y="3.5" width="11" height="7.5" rx="1"/>
        <path d="M1.8 4 L7 8 L12.2 4"/>
      </svg>
    </div>
    <p class="contact contact-phone">0481 526 704</p>
    <p class="contact contact-email">colinbarrow@verdantterraces.example.au</p>
    <div class="front-band"></div>
  </section>

  <section class="card card-back" aria-label="Card back">
    <span class="back-dot"></span>
    <span class="back-wordmark">Verdant<br>Terraces</span>
  </section>
</main>
</body>
</html>
```